Brightfen Business Card Redesign & Logo Update

We need to update our business cards to something more modern and fresh. Brightfen can provide the current color schemes and old design examples, but welcome creativity in helping us with this redesign. PLEASE NOTE that we no longer utilize the "tree" and/or "leaf" imagery in our branding. If able would apprecaite an update on the quality of our "words only" logo in Ai. / PNG formats too.

Target Market(s)

Investors, landowners, corporate partners, contractors

Industry/Entity Type

Environmental Restoration & Conservation

Contact Information for Business Card

Logo, persons name, title, mailing address, phone and email, website url

Font styles to use
Other font styles liked:
• Merriweather

Requirements
Nice to have
• Logo, persons name, title, mailing address, phone and email, website url, but open to ideams
Should not have
• No all back backgrounds

```html
<!DOCTYPE html>
<html lang="en">
<head>
<meta charset="utf-8">
<title>Brightfen Business Cards</title>
<link rel="stylesheet" href="https://fonts.googleapis.com/css2?family=Open+Sans:wght@400;600;700;800&display=swap">
<style>
  :root {
    --green: #137b3f;
    --orange: #ee8122;
    --ink: #151515;
    --paper: #ffffff;
    --backdrop: #e6e8eb;
  }
  * { margin: 0; padding: 0; box-sizing: border-box; }
  html, body { width: 1200px; height: 780px; overflow: hidden; }
  body {
    background: var(--backdrop);
    font-family: "Open Sans", Arial, sans-serif;
    color: var(--ink);
    position: relative;
  }
  .card {
    position: absolute;
    top: 230px;
    width: 560px;
    height: 320px;
    background: var(--paper);
    box-shadow: 0 6px 18px rgba(0,0,0,0.18);
    overflow: hidden;
  }
  .card--front { left: 20px; }
  .card--back { left: 620px; }

  .wordmark { display: flex; flex-direction: column; align-items: flex-start; }
  .wordmark__name {
    font-weight: 800;
    color: var(--green);
    text-transform: uppercase;
    letter-spacing: 1px;
    line-height: 1;
  }
  .wordmark__tagline {
    font-weight: 700;
    text-transform: uppercase;
    color: var(--ink);
    line-height: 1;
  }
  .card--front .wordmark {
    position: absolute; left: 50%; top: 50%;
    transform: translate(-50%, -50%);
  }
  .card--front .wordmark__name { font-size: 74px; }
  .card--front .wordmark__tagline { font-size: 17.5px; letter-spacing: 1.6px; margin-top: 8px; }

  .card--back .wordmark { position: absolute; left: 34px; top: 118px; }
  .card--back .wordmark__name { font-size: 37px; }
  .card--back .wordmark__tagline { font-size: 8.7px; letter-spacing: 0.7px; margin-top: 5px; }

  .divider {
    position: absolute; left: 272px; top: 66px;
    width: 1.5px; height: 130px; background: var(--ink);
  }
  .contact { position: absolute; left: 296px; top: 70px; }
  .contact__name { font-size: 21px; font-weight: 700; line-height: 1.1; }
  .contact__first { color: var(--green); }
  .contact__last { color: var(--orange); }
  .contact__title { font-size: 12.5px; margin-top: 3px; }
  .contact__list { list-style: none; margin-top: 16px; }
  .contact__item {
    display: flex; align-items: center; gap: 8px;
    font-size: 12px; line-height: 1; margin-bottom: 7px;
  }
  .contact__icon { width: 13px; height: 13px; flex: none; }

  .swoosh { position: absolute; left: 0; top: 0; }
</style>
</head>
<body>
  <section class="card card--front" aria-label="Card front">
    <div class="wordmark">
      <span class="wordmark__name">Brightfen</span>
      <span class="wordmark__tagline">Environmental Credit Company</span>
    </div>
  </section>

  <section class="card card--back" aria-label="Card back">
    <svg class="swoosh" width="560" height="320" viewBox="0 0 560 320" aria-hidden="true">
      <path d="M0,262 C200,252 400,205 560,168 L560,320 L0,320 Z" fill="var(--green)"/>
      <path d="M230,232 C380,205 480,176 560,146 L560,156 C470,188 370,214 230,232 Z" fill="var(--orange)"/>
    </svg>

    <div class="wordmark">
      <span class="wordmark__name">Brightfen</span>
      <span class="wordmark__tagline">Environmental Credit Company</span>
    </div>

    <div class="divider"></div>

    <div class="contact">
      <p class="contact__name"><span class="contact__first">Lenka</span> <span class="contact__last">Dvorakova</span></p>
      <p class="contact__title">Managing Director</p>
      <ul class="contact__list">
        <li class="contact__item">
          <svg class="contact__icon" viewBox="0 0 16 16" aria-hidden="true"><path d="M3.5 1.5l2.5 0 1 3.5-1.6 1.2a8 8 0 0 0 4.4 4.4L11 9l3.5 1v2.5c0 1-1 2-2 2C7 14.5 1.5 9 1.5 3.5c0-1 1-2 2-2z" fill="var(--green)"/></svg>
          (555) 014-2290
        </li>
        <li class="contact__item">
          <svg class="contact__icon" viewBox="0 0 16 16" aria-hidden="true"><rect x="1" y="3" width="14" height="10" rx="1.5" fill="var(--green)"/><path d="M1.5 4l6.5 5 6.5-5" fill="none" stroke="#fff" stroke-width="1.3"/></svg>
          info@brightfen.com
        </li>
        <li class="contact__item">
          <svg class="contact__icon" viewBox="0 0 16 16" aria-hidden="true"><circle cx="8" cy="8" r="7" fill="var(--green)"/><path d="M1 8h14M8 1c-3 3.5-3 10.5 0 14M8 1c3 3.5 3 10.5 0 14" fill="none" stroke="#fff" stroke-width="1"/></svg>
          www.brightfen.com
        </li>
      </ul>
    </div>
  </section>
</body>
</html>
```